Business Card & Email Signature Design || Upmarket + Luxury

Rima Vale Honey, a New Zealand Manuka Honey company needs a Business Card & Email Signature design.

Our logo's are attached in Gold & Black versions, feel free to be creative with how you use the logo and it's patterns in your design.

Style:
- Looking for an Elegant, Luxurious, Upmarket feel.
- Black/Matte Black Card, Gold Foil, UV Embossing

Information to Add:

- Logo
- Company Name: Rima Vale Honey
- Name: Martin Holloway
- Title: Creative Director
- Phone: +64 2815 96 417
- Email: martin@rimavalehoney.example.nz
- Website: www.rimavalehoney.example.nz

- Socials: ***For email Signature Only***
- Facebook: https://www.facebook.com/rimavalehoney/
- Instagram: https://www.instagram.com/rimavalehoney/

Target Market(s)

Asia/Europe Luxury, Upmarket

Contact Information for Business Card

- Logo
- Name: Martin Holloway
- Phone: +64 2815 96 417

Font styles to use
Other font styles liked:
• Champagne & Limousines (Attached)

Requirements
Must have
• Business Card & Email Signature Design.

Looking for a Sleek, Luxury, Upmarket Design.

```html
<!DOCTYPE html>
<html lang="en">
<head>
<meta charset="utf-8">
<title>Rima Vale Honey — Business Card</title>
<link href="https://fonts.googleapis.com/css2?family=Cinzel:wght@500&family=Josefin+Sans:wght@300;400&display=swap" rel="stylesheet">
<style>
  :root {
    --backdrop: #a7adae;
    --card-black: #161616;
    --card-edge: #0c0c0c;
    --gold: #d9b53a;
    --gold-bright: #f0c419;
    --gold-line: #b89a4a;
    --leaf-green: #8cc63f;
  }
  * { margin: 0; padding: 0; box-sizing: border-box; }
  html, body {
    width: 1200px;
    height: 824px;
    overflow: hidden;
    background: var(--backdrop);
  }
  .stage {
    position: relative;
    width: 1200px;
    height: 824px;
    display: flex;
    align-items: center;
    justify-content: center;
    gap: 50px;
  }
  .card {
    position: relative;
    width: 525px;
    height: 300px;
    background: var(--card-black);
    border: 1px solid var(--card-edge);
  }
  .card-front .gold-frame {
    position: absolute;
    inset: 14px;
    border: 1px solid var(--gold-line);
  }
  .front-content {
    position: absolute;
    inset: 0;
    display: flex;
    flex-direction: column;
    align-items: center;
    justify-content: center;
    text-align: center;
    padding-top: 4px;
  }
  .brand-mark {
    display: flex;
    align-items: center;
    gap: 6px;
    margin-bottom: 12px;
    font-family: "Josefin Sans", sans-serif;
    font-weight: 400;
    font-size: 9px;
    letter-spacing: 2px;
    text-transform: uppercase;
    color: var(--gold);
  }
  .brand-mark .dot {
    width: 7px;
    height: 7px;
    border-radius: 50%;
    background: var(--gold);
  }
  .person-name {
    font-family: "Cinzel", serif;
    font-weight: 500;
    font-size: 22px;
    letter-spacing: 1px;
    color: var(--gold-bright);
    text-transform: uppercase;
  }
  .person-title {
    font-family: "Josefin Sans", sans-serif;
    font-weight: 400;
    font-size: 12px;
    color: var(--gold-bright);
    margin-top: 4px;
    margin-bottom: 8px;
  }
  .contact-line {
    font-family: "Josefin Sans", sans-serif;
    font-weight: 400;
    font-size: 11.5px;
    line-height: 1.55;
    color: var(--leaf-green);
  }
  .card-back {
    display: flex;
    align-items: center;
    justify-content: center;
  }
  .seal {
    width: 150px;
    height: 150px;
    border: 2px solid var(--gold);
    border-radius: 50%;
    display: flex;
    align-items: center;
    justify-content: center;
    text-align: center;
    font-family: "Josefin Sans", sans-serif;
    font-weight: 400;
    font-size: 13px;
    letter-spacing: 2.5px;
    line-height: 1.6;
    text-transform: uppercase;
    color: var(--gold);
    padding: 20px;
  }
</style>
</head>
<body>
  <main class="stage">
    <section class="card card-front" aria-label="Business card front">
      <div class="gold-frame"></div>
      <div class="front-content">
        <div class="brand-mark"><span class="dot"></span>Rima Vale Honey</div>
        <h1 class="person-name">Martin Holloway</h1>
        <p class="person-title">Creative Director</p>
        <p class="contact-line">+64 2815 96 417 | martin@rimavalehoney.example.nz</p>
        <p class="contact-line">www.rimavalehoney.example.nz</p>
      </div>
    </section>
    <section class="card card-back" aria-label="Business card back">
      <div class="seal">Rima Vale Honey</div>
    </section>
  </main>
</body>
</html>
```